Trovanta Overview and Demo Presentation

Objective:
Create a bold, visually engaging PowerPoint deck to present Trovanta’s sales process and system demo to local movers, emphasizing ease of use, increased profitability, and operational efficiency.
Key Elements:
• Design: High-impact graphics with Trovanta branding, minimal text, and clean layouts.
• Content: Step-by-step sales process, key selling points, system demo walkthrough, and a compelling call-to-action.
• Live Demo: Showcase Trovanta’s platform, focusing on instant guaranteed pricing, streamlined booking, and support features.
Deliverables:
A dynamic presentation designed to educate and convert local movers into Trovanta partners, ensuring seamless flow and strong audience engagement.

Target Market(s)

Local Movers

Industry/Entity Type

Household Goods Moving

Font styles to use
Sans Serif

Colors
0054AA
0677BA
7BADD7
CADEEF
E8F1F8
FFC000
F8CF3A
FAE287
FDF2CF
FEFAEE

Requirements
Must have
• Project Brief: Trovanta Sales Process Presentation Objective: Create a bold, visually engaging PowerPoint deck to present Trovanta’s sales process and system demo to local movers, emphasizing ease of use, increased profitability, and operational efficiency. Key Elements: • Design: High-impact graphics with Trovanta branding, minimal text, and clean layouts. • Content: Step-by-step sales process, key selling points, system demo walkthrough, and a compelling call-to-action. • Live Demo: Showcase Trovanta’s platform, focusing on instant guaranteed pricing, streamlined booking, and support features. Deliverables: A dynamic presentation designed to educate and convert local movers into Trovanta partners, ensuring seamless flow and strong audience engagement.

```html
<!DOCTYPE html>
<html lang="en">
<head>
<meta charset="utf-8">
<title>Trovanta Partner Overview Deck</title>
<link rel="stylesheet" href="https://fonts.googleapis.com/css2?family=Kumbh+Sans:wght@400;500;600;700;800&display=swap">
<style>
:root{
  --backdrop:#6a6a6a;
  --navy:#1b3a8c;
  --royal:#1a3e9a;
  --bright:#1447c9;
  --orange:#f6a42c;
  --ink:#2b2b2b;
  --muted:#555;
  --pale:#dfe8f8;
  --white:#fff;
}
*{box-sizing:border-box;margin:0;padding:0}
html,body{width:986px;height:1200px;overflow:hidden}
body{background:var(--backdrop);font-family:"Kumbh Sans",sans-serif;color:var(--ink);position:relative}
.slide{position:absolute;width:718px;height:404px;background:var(--white);transform:scale(.568);transform-origin:0 0;overflow:hidden;box-shadow:0 6px 18px rgba(0,0,0,.35)}
.col-l{left:73.8px}.col-r{left:504.4px}
.row-1{top:107.9px}.row-2{top:359.5px}.row-3{top:611.2px}.row-4{top:862.8px}
.abs{position:absolute}
.brand{display:flex;align-items:center;gap:8px;font-weight:700;color:var(--bright)}
.brand i{display:block;background:currentColor}
.footer-brand{left:28px;top:365px;font-size:19px}
.footer-brand i{width:12px;height:12px}
.footer-rule{left:154px;right:56px;top:377px;height:1px;background:var(--navy);opacity:.6}
.page-num{width:22px;height:22px;border-radius:50%;background:var(--bright);color:#fff;font-size:11px;font-weight:600;display:flex;align-items:center;justify-content:center;left:684px;top:366px}
.tag{background:var(--orange);color:#fff;font-weight:800;padding:0 10px;line-height:44px;font-size:34px;letter-spacing:.3px}
.head{font-weight:800;color:var(--navy);font-size:34px;line-height:44px}
.title-row{display:flex;gap:8px;left:32px;top:25px}
.photo{background:linear-gradient(135deg,#c9a27a,#8a6a4c)}
p.body{font-size:13.6px;line-height:21.4px;text-align:justify;color:var(--ink)}

/* cover */
.cover{background:var(--royal);color:#fff}
.cover .brand{color:#fff;left:92px;top:100px;font-size:34px}
.cover .brand i{width:20px;height:20px}
.cover h1{left:92px;top:182px;font-size:32px;line-height:43px;font-weight:700}
.cover .sub{left:92px;top:287px;font-size:16px}
.cover .photo{left:431px;top:13px;width:272px;height:377px;clip-path:polygon(0 0,100% 10%,100% 100%,0 100%);background:linear-gradient(180deg,#d9d2c8 0%,#8a8178 45%,#2f4f9a 70%,#4b4640 100%)}
.cover .page-num{background:#fff;color:var(--royal);top:370px}

/* opportunity */
.lead{font-size:22px;font-weight:800;color:var(--navy);left:43px;top:76px}
.why{font-size:16px;left:43px;top:110px;font-weight:500}
.dash{left:418px;top:180px;width:284px;height:157px;border-radius:8px;background:linear-gradient(180deg,#f4f6fb 0%,#e7ecf6 60%,#c9d6ef 100%);box-shadow:0 2px 10px rgba(0,0,0,.18)}
.kpi{font-size:9px;text-align:center;line-height:10px;width:80px;color:var(--ink)}
.kpi b{display:block;font-size:13px;line-height:16px;font-weight:600}

/* revolutionizing */
.stat-box{left:413px;width:284px;height:100px;border-radius:4px;color:#fff}
.stat-box .big{position:absolute;top:14px;font-size:19px;font-weight:500}
.stat-box .small{position:absolute;top:46px;font-size:11px;line-height:14px}
.pill{position:absolute;left:106px;top:38px;width:72px;height:24px;border-radius:12px;font-size:10.5px;display:flex;align-items:center;justify-content:center}

/* solution */
.feat h3{font-size:13px;font-weight:600;margin-bottom:6px;color:var(--ink)}
.feat p{font-size:8px;line-height:13px;color:var(--muted)}

/* vision */
.dia-text{text-align:center}
.dia-text h3{font-size:14px;font-weight:600;margin:6px 0 6px}
.dia-text .strong{font-size:8.5px;font-weight:700;line-height:14px}
.dia-text .fine{font-size:6.6px;line-height:10.6px;margin-top:4px}

/* thanks */
.thanks{background:var(--royal);color:#fff}
.thanks .photo{left:0;top:0;width:470px;height:404px;background:linear-gradient(90deg,#3a4a6a 0%,#7c6a66 40%,#b27655 60%,rgba(26,62,154,0) 100%)}
.contact{font-size:13px;line-height:19px;left:473px}
</style>
</head>
<body>

<!-- 01 cover -->
<section class="slide cover col-l row-1">
  <div class="abs brand"><i></i>Trovanta</div>
  <h1 class="abs">Moving For The<br>Next Generation</h1>
  <div class="abs sub">Partner Overview Presentation</div>
  <div class="abs photo" role="img" aria-label="Two movers in blue overalls walking toward a townhouse beside a white van"></div>
  <div class="abs page-num">01</div>
</section>

<!-- 05 opportunity -->
<section class="slide col-r row-1">
  <div class="abs tag" style="left:32px;top:25px">THE OPPORTUNITY</div>
  <div class="abs lead">TARGETING B2I LOCAL MOVERS</div>
  <div class="abs why">WHY B2I FIRST?</div>
  <div class="abs" style="left:43px;top:142px;width:330px">
    <p class="body">B2I (local movers) represents the most immediate and scalable opportunity for Trovanta. The software’s AI-driven pricing and capacity optimization allow local movers to keep their trucks busy and maximize revenue.<br>We’ve proven the B2I model... by adding one new B2I customer per week, each averaging four moves a month or 72 moves per year. This provides consistent, recurring revenue for Trovanta.</p>
  </div>
  <svg class="abs" style="left:410px;top:50px" width="300" height="140" viewBox="0 0 300 140">
    <polygon points="55,35 110,86 55,137 0,86" fill="#fff" stroke="#1b3a8c"/>
    <polygon points="147,5 200,57 147,110 94,57" fill="#1b3a8c"/>
    <polygon points="238,35 293,86 238,137 183,86" fill="#fff" stroke="#1b3a8c"/>
  </svg>
  <div class="abs kpi" style="left:425px;top:113px"><b>XXX</b>moves/year<br>from new B2I<br>customers</div>
  <div class="abs kpi" style="left:517px;top:84px;color:#fff"><b>XXX</b>Estimated<br>Gross Profit</div>
  <div class="abs kpi" style="left:608px;top:113px"><b>XXX</b>Projected EBITDA<br>over next 24<br>months</div>
  <div class="abs dash" role="img" aria-label="Pricing software dashboard with market table and area chart"></div>
  <div class="abs brand footer-brand"><i></i>Trovanta</div>
  <div class="abs footer-rule"></div>
  <div class="abs page-num">05</div>
</section>

<!-- 02 revolutionizing -->
<section class="slide col-l row-2">
  <div class="abs tag" style="left:32px;top:27px">REVOLUTIONIZING</div>
  <div class="abs head" style="left:44px;top:70px">THE MOVING<br>INDUSTRY WITH AI</div>
  <div class="abs" style="left:44px;top:165px;width:316px">
    <p class="body" style="font-size:14px;line-height:23.5px">Trovanta is transforming the $90-100B moving industry by leveraging AI, GPS, and automated compliance to deliver the first instant guaranteed pricing platform. We’re cutting out inefficiencies and middlemen to improve costs and service quality.</p>
  </div>
  <svg class="abs" style="left:379px;top:14px" width="339" height="354" viewBox="0 0 339 354">
    <polygon points="0,0 60,40 60,314 0,354" fill="#dfe8f8"/>
    <polygon points="339,0 280,40 280,314 339,354" fill="#dfe8f8"/>
  </svg>
  <div class="abs stat-box" style="top:70px;background:var(--navy)">
    <div class="big" style="left:26px">$1.9M</div>
    <div class="small" style="left:26px">Revenue<br>Successfully<br>Raised</div>
    <div class="pill" style="background:var(--orange);color:var(--navy)">To Build</div>
    <div class="big" style="left:206px">$5</div>
    <div class="small" style="left:206px">Appraised<br>Tech Stack</div>
  </div>
  <div class="abs" style="left:413px;width:284px;top:178px;text-align:center;font-size:17px;font-weight:600;color:var(--navy)">PROVEN MODEL</div>
  <div class="abs stat-box" style="top:212px;background:var(--orange)">
    <div class="big" style="left:26px">$500K</div>
    <div class="small" style="left:26px">Additional<br>Raise</div>
    <div class="pill" style="background:var(--navy);color:#fff">To Prove</div>
    <div class="big" style="left:206px">B21</div>
    <div class="small" style="left:206px">Successful<br>Model</div>
  </div>
  <div class="abs brand footer-brand"><i></i>Trovanta</div>
  <div class="abs footer-rule"></div>
  <div class="abs page-num">02</div>
</section>

<!-- 06 solution -->
<section class="slide col-r row-2">
  <div class="abs title-row"><span class="tag">TROVANTA</span><span class="head">SOLUTION</span></div>
  <svg class="abs" style="left:220px;top:95px" width="224" height="210" viewBox="0 0 224 210">
    <polygon points="111,5 193,87 111,169 29,87" fill="#fff" stroke="#1447c9"/>
    <rect x="101" y="77" width="20" height="20" fill="#1447c9" transform="rotate(45 111 87)"/>
    <polygon points="61,17 83,39 61,61 39,39" fill="#1b3a8c"/>
    <polygon points="162,17 184,39 162,61 140,39" fill="#f6a42c"/>
    <polygon points="61,120 83,142 61,164 39,142" fill="#f6a42c"/>
    <polygon points="162,120 184,142 162,164 140,142" fill="#1b3a8c"/>
    <polygon points="112,158 134,180 112,202 90,180" fill="#1447c9"/>
    <g fill="#fff" font-family="Kumbh Sans,sans-serif" font-size="10" text-anchor="middle">
      <text x="61" y="43">01</text><text x="162" y="43">03</text>
      <text x="61" y="146">02</text><text x="162" y="146">04</text>
      <text x="112" y="184">05</text>
    </g>
  </svg>
  <div class="abs feat" style="right:469px;top:107px;width:200px;text-align:right">
    <h3>On-Demand Process</h3>
    <p>Trovanta automatically audits: Compliance, Insurance, Regulatory, Bonding, Background checks, and Quality.</p>
  </div>
  <div class="abs feat" style="left:415px;top:107px;width:190px">
    <h3>Book Now Pay Later</h3>
    <p>Moving has a high price tag, but no one has ever offered a pay later solution. Much less a no credit check offer.</p>
  </div>
  <div class="abs feat" style="right:469px;top:210px;width:200px;text-align:right">
    <h3>One Point of Contact</h3>
    <p>Today moves are sold from broker to broker until it’s finally sold to a mover. Many entities involved means a confusing line of correspondence for the customer.</p>
  </div>
  <div class="abs feat" style="left:415px;top:210px;width:200px">
    <h3>GPS Tracking</h3>
    <p>Online retail has conditioned consumers to expect real-time tracking of goods. Only Trovanta enables you to track all of your belongings door to door.</p>
  </div>
  <div class="abs feat" style="left:217px;top:302px;width:230px;text-align:center">
    <h3>Simple Honest Pricing</h3>
    <p>Trovanta’s proprietary algorithms and data are backed up by a checks and balances process giving the first instant pricing solution that won’t change.</p>
  </div>
  <div class="abs brand footer-brand"><i></i>Trovanta</div>
  <div class="abs footer-rule"></div>
  <div class="abs page-num">06</div>
</section>

<!-- 03 vision -->
<section class="slide col-l row-3">
  <div class="abs title-row"><span class="tag">OUR</span><span class="head">VISION</span></div>
  <div class="abs" style="left:318px;top:24px;width:350px;font-size:13.5px;line-height:21px">The traditional moving industry is broken, outdated, inefficient, and unable to change.</div>
  <svg class="abs" style="left:24px;top:84px" width="672" height="272" viewBox="0 0 672 272">
    <polygon points="135,2 269,136 135,270 1,136" fill="#fff" stroke="#1b3a8c"/>
    <polygon points="536,2 670,136 536,270 402,136" fill="#fff" stroke="#1b3a8c"/>
    <polygon points="336,2 470,136 336,270 202,136" fill="#1b3a8c"/>
    <circle cx="135" cy="56" r="7" fill="none" stroke="#f6a42c" stroke-width="3"/>
    <circle cx="135" cy="56" r="2.5" fill="#f6a42c"/>
    <circle cx="336" cy="56" r="10" fill="none" stroke="#f6a42c" stroke-width="2.5"/>
    <circle cx="336" cy="56" r="4" fill="#f6a42c"/>
    <rect x="525" y="49" width="22" height="13" rx="3" fill="#f6a42c"/>
  </svg>
  <div class="abs dia-text" style="left:79px;top:152px;width:160px">
    <h3>Our Vision</h3>
    <div class="strong">Revolutionize the moving industry by providing great value to everyone involved</div>
    <div class="fine">Trovanta Customers - Consumers, Movers, Corporate Clients, and Relocation Management Companies all receive better value with Trovanta than anywhere else.</div>
  </div>
  <div class="abs dia-text" style="left:280px;top:152px;width:160px;color:#fff">
    <h3 style="color:var(--orange)">Our Mission</h3>
    <div class="strong">Disrupt a $86B sleepy giant of an inefficient industry</div>
    <div class="fine">Trovanta’s deep understanding of the professional moving industry, supported by extensive market research has set Trovanta up for ultimate success in disrupting this industry by creating cost-saving efficiencies throughout.</div>
  </div>
  <div class="abs dia-text" style="left:480px;top:152px;width:160px">
    <h3>Our Goal</h3>
    <div class="strong">Becoming the moving platform of choice</div>
    <div class="fine">As Trovanta’s market share grows, the customer acquisition cost and operational cost plummets. This creates even more market penetration, more efficiencies, and exponential growth.</div>
  </div>
  <div class="abs brand footer-brand"><i></i>Trovanta</div>
  <div class="abs footer-rule"></div>
  <div class="abs page-num">03</div>
</section>

<!-- 07 future -->
<section class="slide col-r row-3">
  <div class="abs title-row"><span class="tag">TROVANTA</span><span class="head">THE FUTURE OF MOVING</span></div>
  <div class="abs photo" style="left:302px;top:79px;width:398px;height:268px;background:linear-gradient(90deg,rgba(255,255,255,1) 0%,#e9ddcf 18%,#c79d6f 50%,#a9815c 75%,#e6e1da 100%)" role="img" aria-label="Couple packing cardboard moving boxes in a bright home"></div>
  <div class="abs" style="left:46px;top:133px;font-size:19px;font-weight:500">CUTTING OUT MIDDLEMEN</div>
  <div class="abs" style="left:46px;top:180px;width:270px;font-size:13.6px;line-height:21.4px">Trovanta’s direct-to-consumer model eliminates van lines, agents, &amp; brokers. Customers connect directly with professional movers, reducing layers of markup and ensuring clarity.</div>
  <div class="abs brand footer-brand"><i></i>Trovanta</div>
  <div class="abs footer-rule"></div>
  <div class="abs page-num">07</div>
</section>

<!-- 04 about -->
<section class="slide col-l row-4">
  <div class="abs title-row"><span class="tag">ABOUT</span><span class="head">US</span></div>
  <div class="abs" style="left:40px;top:88px;width:320px">
    <p class="body">Trovanta is the next logical evolution in professional moving. Professional moving clients have battled soaring prices, acute capacity problems and deteriorating service levels.<br>Trovanta was founded by lifelong moving professionals who have developed the answer to better moving services. Poised as THE industry disruptor, we deliver faster, offer guaranteed prices and even offer no credit check financing options. We are a technology first organization using proprietary software to deliver moving's best service experience.</p>
  </div>
  <svg class="abs" style="left:379px;top:14px" width="339" height="354" viewBox="0 0 339 354">
    <polygon points="0,0 58,50 58,304 0,354" fill="#1447c9"/>
    <polygon points="339,0 281,50 281,304 339,354" fill="#1447c9"/>
  </svg>
  <div class="abs photo" style="left:406px;top:93px;width:287px;height:196px;background:linear-gradient(135deg,#5a3a2a,#b07a4e 55%,#d9b48a)" role="img" aria-label="Woman taping a cardboard box in front of a brick wall"></div>
  <div class="abs brand footer-brand"><i></i>Trovanta</div>
  <div class="abs footer-rule"></div>
  <div class="abs page-num">04</div>
</section>

<!-- 08 thanks -->
<section class="slide thanks col-r row-4">
  <div class="abs photo" role="img" aria-label="City skyline at dusk with light trails on a curving highway"></div>
  <div class="abs brand" style="left:420px;top:58px;font-size:17px;color:#fff"><i style="width:11px;height:11px"></i>Trovanta</div>
  <div class="abs" style="left:417px;top:96px;display:flex;gap:6px">
    <span class="tag" style="font-size:27px;line-height:40px;padding:0 8px">THANK</span>
    <span style="font-size:27px;line-height:40px;font-weight:800">YOU</span>
  </div>
  <svg class="abs" style="left:416px;top:180px" width="48" height="170" viewBox="0 0 48 170">
    <polygon points="24,2 46,24 24,46 2,24" fill="none" stroke="#fff"/>
    <path d="M24 14a6 6 0 0 0-6 6c0 5 6 11 6 11s6-6 6-11a6 6 0 0 0-6-6z" fill="#fff"/>
    <polygon points="24,61 46,83 24,105 2,83" fill="#f6a42c"/>
    <path d="M19 77c1 5 4 9 10 11l2-3-3-2-2 1c-2-1-3-3-4-5l1-2-2-3z" fill="#fff"/>
    <polygon points="24,124 46,146 24,168 2,146" fill="none" stroke="#fff"/>
    <circle cx="24" cy="146" r="6" fill="none" stroke="#fff" stroke-width="1.5"/>
    <line x1="18" y1="146" x2="30" y2="146" stroke="#fff"/>
  </svg>
  <div class="abs contact" style="top:182px">480 Harlow St., Suite 12<br>Riverton, KS 66101</div>
  <div class="abs contact" style="top:252px;font-size:15px">(800) 555-0142</div>
  <div class="abs contact" style="top:307px;font-size:12px">trovanta.com<br>support@trovanta.com</div>
  <div class="abs page-num" style="background:var(--orange);color:var(--royal)">08</div>
</section>

</body>
</html>
```